BrivoTerna. Lantern of the Steady Harvest. Business card

Professional business card for BrivoTerna (Lantern of the Steady Harvest)
My rationale: Strategy-> Execution-> Results-> Value that lead to the BrivoTerna name: We put the Lantern of the Steady Harvest.
We deliver value to our customers helping them at defining a good strategy (cyan arrow). 90% of well formulated strategies fail due to poor execution so we also consider strategical execution very important (green arrow). Due to the execution we obtain the results (blue arrow). Finally, the results provide feedback to redefine strategy, and the new strategy has to be executed and new results obtained providing new feedback and on and on. It's like a wheel that finally, must create corporate value: value for shareholders, staholders, employees, providers...-

Target Market(s)

CEOs and steering comitees , invewrnent funds

Industry/Entity Type

Business Consultant

Contact Information for Business Card

Teodoro Vinsquel
CEO & Founder
teodoro.vinsquel@brivoterna-example.com
Mobile: +34 655.803.912
www.brivoterna-example.com

Colors

Designer to choose colors to be used in the design.

Requirements
Nice to have
• Nice to hace the words: Strategy, execution, results
• Nice to vave the claim: Lantern of the Steady Harvest
• The three colors should be shown:
• cyan for STRATEGY
• green for EXECUTION
• blue for RESULTS
Should not have
• Complete black background

```html
<!DOCTYPE html>
<html lang="en">
<head>
<meta charset="utf-8">
<title>BrivoTerna – Business Card</title>
<link rel="stylesheet" href="https://fonts.googleapis.com/css2?family=Arimo:wght@400;700&display=swap">
<style>
  :root {
    --stage: #d6d7d9;
    --brand-blue: #00309a;
    --brand-green: #9acd32;
    --brand-cyan: #15a9e8;
    --paper: #ffffff;
    --ink: #333333;
    --card-shadow: 0 2px 4px rgba(0,0,0,.35);
  }
  * { margin: 0; padding: 0; box-sizing: border-box; }
  html, body {
    width: 1200px; height: 802px; overflow: hidden;
    background: var(--stage);
    font-family: "Arimo", Arial, sans-serif;
  }
  .canvas { position: relative; width: 1200px; height: 802px; }
  .card {
    position: absolute; top: 274px; width: 442px; height: 264px;
    box-shadow: var(--card-shadow); overflow: hidden;
  }
  .card--front { left: 136px; background: var(--brand-blue); color: var(--paper); }
  .card--back { left: 624px; background: var(--paper); }

  .growth-motif { position: absolute; inset: 0; }

  .front__brand {
    position: absolute; left: 24px; top: 36px;
    font-size: 37px; font-weight: 700; letter-spacing: -1px; line-height: 1;
  }
  .front__claim {
    position: absolute; left: 24px; top: 81px;
    font-size: 11.5px; letter-spacing: .2px;
  }
  .person { position: absolute; left: 24px; top: 140px; }
  .person__name { font-size: 17.5px; line-height: 1.1; }
  .person__role { font-size: 12.5px; margin-top: 1px; }
  .contact { position: absolute; left: 24px; top: 186px; list-style: none; }
  .contact__item {
    display: flex; align-items: center; gap: 4px;
    font-size: 12.3px; line-height: 16px;
  }
  .contact__icon { width: 12px; height: 12px; flex: none; fill: var(--paper); }

  .back__brand {
    position: absolute; left: 0; right: 0; top: 140px;
    text-align: center; color: var(--brand-blue);
    font-size: 44px; font-weight: 700; letter-spacing: -1.5px; line-height: 1;
  }
  .back__mark {
    position: absolute; left: 199px; top: 70px; width: 44px; height: 44px;
    border-radius: 50%; background: var(--brand-blue);
  }
  .back__claim {
    position: absolute; left: 0; right: 0; top: 206px;
    text-align: center; color: var(--ink);
    font-size: 13px; letter-spacing: .3px;
  }
  .color-band {
    position: absolute; left: 0; right: 0; bottom: 0; height: 9px; display: flex;
  }
  .color-band__results { width: 31%; background: var(--brand-blue); }
  .color-band__execution { width: 37.5%; background: var(--brand-green); }
  .color-band__strategy { flex: 1; background: var(--brand-cyan); }
</style>
</head>
<body>
<main class="canvas">
  <section class="card card--front">
    <svg class="growth-motif" viewBox="0 0 442 264" role="img" aria-label="Rising growth arrow decoration in white, green and cyan">
      <defs>
        <linearGradient id="motifFill" x1="0" y1="1" x2="1" y2="0">
          <stop offset="0" stop-color="#ffffff"/>
          <stop offset=".55" stop-color="#e9f5d3"/>
          <stop offset="1" stop-color="#9acd32"/>
        </linearGradient>
      </defs>
      <path d="M190 264 C300 230 340 150 355 0 L442 0 L442 264 Z" fill="url(#motifFill)"/>
    </svg>

    <div class="front__brand">BrivoTerna</div>
    <div class="front__claim">STRATEGY, EXECUTION, RESULTS</div>

    <div class="person">
      <div class="person__name">Teodoro Vinsquel</div>
      <div class="person__role">CEO &amp; Founder</div>
    </div>

    <ul class="contact">
      <li class="contact__item">
        <svg class="contact__icon" viewBox="0 0 12 12"><path d="M1 4c0-2 2-3 5-3s5 1 5 3l-2 1-1-2H4L3 5zM3 6h6l1 5H2z"/></svg>
        +34 655.803.912
      </li>
      <li class="contact__item">
        <svg class="contact__icon" viewBox="0 0 12 12"><path d="M1 3h10v7H1z" /><path d="M1 3l5 4 5-4" fill="none" stroke="#00309a" stroke-width="1"/></svg>
        teodoro.vinsquel@brivoterna-example.com
      </li>
      <li class="contact__item">
        <svg class="contact__icon" viewBox="0 0 12 12"><circle cx="6" cy="6" r="5.5"/><path d="M3 3c2 1 1 3 3 3s1 3 2 4M8 2c0 2 2 2 3 2" fill="none" stroke="#00309a" stroke-width="1"/></svg>
        www.brivoterna-example.com
      </li>
    </ul>
  </section>

  <section class="card card--back">
    <span class="back__mark"></span>
    <div class="back__brand">BrivoTerna</div>
    <div class="back__claim">LANTERN OF THE STEADY HARVEST</div>
    <div class="color-band">
      <span class="color-band__results"></span>
      <span class="color-band__execution"></span>
      <span class="color-band__strategy"></span>
    </div>
  </section>
</main>
</body>
</html>
```